Webdesign für Zahnarztpraxis
Zielgruppe
Zahnarztpraxis
Aufgabenstellung
- Klares und übersichtliches Desgin
- Nicht zu verspielt
- Informativ
- Leichte Naviagtion
- Das Design der alten Webseite soll NICHT kopiert werden
- Die Farben Blau und Grün aus dem Logo sollen sich wiederfinden
- Designbeispiele, die dem Kunden gefallen sind https://www.falkmann-ostrup-zahnarztpraxis.de/ und https://www.zahvilkorn.de/

```html
<!DOCTYPE html>
<html lang="de">
<head>
<meta charset="utf-8">
<title>Zahnarztpraxis Dr. Marie Kestner</title>
<link href="https://fonts.googleapis.com/css2?family=Nunito+Sans:wght@400;600;700;800&display=swap" rel="stylesheet">
<style>
:root{
  --blue:#2a9bd8;
  --blue-soft:#e8f4fb;
  --green:#6cbf45;
  --green-soft:#eef8e8;
  --navy:#2b3a4e;
  --text:#4a5566;
  --muted:#6b7686;
  --line:#e3e8ee;
  --page:#dcdcdc;
  --tint:#f7f9fc;
  --red:#e04a4a;
}
*{box-sizing:border-box;margin:0;padding:0}
html,body{width:1200px;height:2913px;overflow:hidden}
body{background:var(--page);font-family:"Nunito Sans",sans-serif;color:var(--text);position:relative}
.block{position:absolute;left:37px;width:1124px;background:#fff}
.center{text-align:center}
h1,h2,h3{color:var(--navy);font-weight:800}
.btn{display:inline-flex;align-items:center;justify-content:center;height:26px;border-radius:4px;font-size:9px;font-weight:700;border:1px solid var(--blue);color:var(--blue);background:#fff}
.btn.solid{background:var(--blue);color:#fff}
.btn.green{border-color:var(--green);color:var(--green)}
.btn.red{border-color:var(--red);color:var(--red)}
.icon{width:36px;height:36px;border-radius:50%;background:var(--blue-soft);display:flex;align-items:center;justify-content:center;margin:0 auto}
.icon.g{background:var(--green-soft)}
.icon svg{width:17px;height:17px;fill:none;stroke:var(--blue);stroke-width:1.6;stroke-linecap:round;stroke-linejoin:round}
.icon.g svg{stroke:var(--green)}

/* header */
.header{top:40px;height:46px;display:flex;align-items:center;justify-content:space-between;padding:0 166px 0 159px}
.brand{display:flex;align-items:center;gap:6px;font-size:14px;font-weight:700;color:var(--blue)}
.brand i{width:14px;height:14px;border-radius:50%;background:var(--green);display:block}
.nav{display:flex;gap:21px;font-size:9px;font-weight:700;color:var(--navy)}

/* hero */
.hero{top:86px;height:590px;overflow:hidden}
.hero-photo{position:absolute;inset:0;background:linear-gradient(160deg,#eef5f9 0%,#e3ecef 35%,#dfe9e4 60%,#f2f5f4 100%)}
.hero-veil{position:absolute;inset:0;background:linear-gradient(180deg,rgba(255,255,255,.85),rgba(255,255,255,.55) 60%,rgba(255,255,255,.75))}
.hero-content{position:absolute;top:28px;left:0;right:0;text-align:center}
.hero h1{font-size:36px;letter-spacing:-.3px}
.hero .sub{font-size:14px;color:var(--muted);margin-top:8px}
.hero .lead{font-size:10.5px;color:var(--text);margin-top:22px;line-height:17px}
.hero .actions{display:flex;gap:10px;justify-content:center;margin-top:16px}
.notice{position:absolute;left:293px;top:439px;width:534px;height:106px;border:1px solid #a9d6ef;border-radius:6px;background:rgba(232,244,251,.7);padding:10px 14px 0 27px;font-size:9px;line-height:12px;color:var(--navy)}
.notice h3{font-size:11.5px;font-weight:600;margin-bottom:4px;position:relative}
.notice h3 svg{position:absolute;left:-17px;top:1px;width:11px;height:11px;fill:none;stroke:var(--navy);stroke-width:1.4}
.notice p{margin-bottom:13px}

/* praxis */
.praxis{top:701px;height:311px}
.sec-title{font-size:21px;padding-top:24px}
.sec-sub{font-size:10.5px;color:var(--muted);margin-top:7px}
.features{display:flex;gap:14px;justify-content:center;margin-top:27px}
.feature{width:195px;height:128px;border:1px solid var(--line);border-radius:6px;padding-top:16px;text-align:center}
.feature h3{font-size:10.5px;font-weight:700;margin-top:13px}
.feature p{font-size:9px;color:var(--muted);line-height:14px;margin:5px 18px 0}

/* leistungen */
.leistungen{top:1036px;height:473px;background:var(--tint)}
.leistungen .sec-title{padding-top:53px}
.services{display:grid;grid-template-columns:repeat(4,165px);grid-auto-rows:80px;gap:10px;width:690px;margin:27px auto 0}
.service{background:#fff;border:1px solid var(--line);border-radius:5px;text-align:center;padding-top:15px}
.service .icon{width:30px;height:30px}
.service .icon svg{width:14px;height:14px}
.service h3{font-size:8.5px;font-weight:700;margin-top:9px}

/* labor & team */
.labor{top:1538px;height:566px}
.team-band{position:absolute;left:0;right:0;top:285px;bottom:0;background:var(--tint)}
.split{position:absolute;width:613px;left:256px;display:flex;gap:21px;align-items:center}
.photo{width:296px;height:199px;border-radius:6px;box-shadow:0 8px 18px rgba(0,0,0,.14);flex:none}
.split-text{width:296px}
.split-text h2{font-size:22px}
.split-text .intro{font-size:10.5px;color:var(--muted);margin-top:9px;line-height:16px}
.split-text .body{font-size:9px;line-height:14.5px;margin-top:16px}
.split-text .btn{margin-top:20px;padding:0 20px}

/* kontakt */
.kontakt{top:2135px;height:591px}
.kontakt .sec-title{padding-top:60px}
.cards{position:absolute;left:256px;top:129px;width:613px;display:grid;grid-template-columns:297px 297px;gap:16px 16px;grid-template-rows:86px 91px 201px}
.card{border:1px solid var(--line);border-radius:6px;padding:14px 15px;font-size:9px;line-height:15px;color:var(--navy)}
.card.hl-blue{border-color:#bfe1f3}
.card.hl-green{border-color:#e1f0d6}
.card h3{font-size:13.5px;font-weight:600;display:flex;align-items:center;gap:6px;margin-bottom:10px}
.card h3 svg{width:12px;height:12px;fill:none;stroke:var(--blue);stroke-width:1.6;stroke-linecap:round;stroke-linejoin:round}
.card a{color:var(--blue);text-decoration:none}
.card .muted{color:var(--muted)}
.hours{display:grid;grid-template-columns:1fr auto;row-gap:4px}
.hours b{font-weight:700}
.hours span{text-align:right}
.card .note{font-size:8px;line-height:12px;color:var(--muted)}
.card .btn.red{height:22px;padding:0 8px;margin-top:3px;font-size:8.5px;gap:4px}
.ext{width:9px;height:9px;fill:none;stroke:currentColor;stroke-width:1.5}

/* footer */
.footer{top:2726px;height:62px;background:var(--tint);border-top:1px solid var(--line);display:flex;align-items:center;justify-content:space-between;padding:0 154px 0 159px}
.foot-left{display:flex;align-items:center;gap:12px}
.foot-name{font-size:9.5px;font-weight:700;color:var(--navy);line-height:12px}
.foot-name small{display:block;font-size:8px;font-weight:400;color:var(--muted)}
.copy{font-size:8px;color:var(--muted);text-align:right;line-height:12px}
</style>
</head>
<body>

<header class="block header">
  <div class="brand"><i></i>Kestner Dental</div>
  <nav class="nav"><span>Unsere Praxis</span><span>Leistungen</span><span>Praxislabor</span><span>Team</span><span>Kontakt</span></nav>
</header>

<section class="block hero">
  <div class="hero-photo" role="img" aria-label="Heller Behandlungsraum der Praxis mit Zahnarztstuhl und Pflanze"></div>
  <div class="hero-veil"></div>
  <div class="hero-content">
    <h1>Zahnarztpraxis Dr. Marie Kestner</h1>
    <p class="sub">Praxis &amp; Dentallabor in Talheim-Wiesenau</p>
    <p class="lead">Prävention und Individualprophylaxe in jeder Altersgruppe!<br>Zahnärztin spricht auch fließend Englisch.</p>
    <div class="actions">
      <span class="btn solid" style="width:111px">Termin vereinbaren</span>
      <span class="btn" style="width:108px">Unsere Leistungen</span>
    </div>
  </div>
  <div class="notice">
    <h3><svg viewBox="0 0 12 12"><circle cx="6" cy="6" r="5"/><path d="M6 3.5v3M6 8.3v.1"/></svg>Wichtige Information für unsere Patienten</h3>
    <p>Liebe Patienten,</p>
    <p>in der Zeit von <b>xx.xx.2025 - einschließlich xx.xx.2025</b> bleibt unsere Praxis geschlossen.</p>
    <p>Die Vertretung in dieser Zeit übernimmt Frau/Herr ... Bitte melden Sie sich im Vorfeld telefonisch an.</p>
  </div>
</section>

<section class="block praxis center">
  <h2 class="sec-title">Unsere Praxis</h2>
  <p class="sec-sub">Ihre Zahngesundheit in kompetenten Händen</p>
  <div class="features">
    <div class="feature">
      <div class="icon"><svg viewBox="0 0 24 24"><rect x="6" y="3" width="12" height="18" rx="1"/><path d="M9 7h6M9 11h6M9 15h6"/></svg></div>
      <h3>Praxis &amp; Labor</h3>
      <p>Praxis &amp; Dentallabor in Talheim-Wiesenau</p>
    </div>
    <div class="feature">
      <div class="icon g"><svg viewBox="0 0 24 24"><circle cx="9" cy="8" r="3.5"/><path d="M3 20c0-3.5 2.7-6 6-6s6 2.5 6 6M16 4.5a3.5 3.5 0 0 1 0 7M18 14c2 .7 3 2.8 3 6"/></svg></div>
      <h3>Für alle Altersgruppen</h3>
      <p>Prävention und Individualprophylaxe in jeder Altersgruppe</p>
    </div>
    <div class="feature">
      <div class="icon"><svg viewBox="0 0 24 24"><circle cx="12" cy="12" r="9"/><path d="M3 12h18M12 3c3 3 3 15 0 18M12 3c-3 3-3 15 0 18"/></svg></div>
      <h3>Englisch sprechend</h3>
      <p>Zahnärztin spricht auch fließend Englisch</p>
    </div>
  </div>
  <span class="btn" style="width:131px;margin-top:21px">Mehr über unsere Praxis</span>
</section>

<section class="block leistungen center">
  <h2 class="sec-title">Unsere Leistungen</h2>
  <p class="sec-sub">Umfassende zahnmedizinische Versorgung für die ganze Familie</p>
  <div class="services">
    <div class="service"><div class="icon"><svg viewBox="0 0 24 24"><path d="M6 3v6a5 5 0 0 0 10 0V3M11 14v2a4 4 0 0 0 8 0v-2"/><circle cx="19" cy="12" r="2"/></svg></div><h3>Zahnärztliche Diagnostik</h3></div>
    <div class="service"><div class="icon"><svg viewBox="0 0 24 24"><path d="M12 3l7 3v6c0 4.5-3 7.5-7 9-4-1.5-7-4.5-7-9V6z"/></svg></div><h3>Individualprophylaxe</h3></div>
    <div class="service"><div class="icon"><svg viewBox="0 0 24 24"><path d="M11 4l1.8 5.2L18 11l-5.2 1.8L11 18l-1.8-5.2L4 11l5.2-1.8zM18 3v4M16 5h4"/></svg></div><h3>Professionelle Zahnreinigung</h3></div>
    <div class="service"><div class="icon"><svg viewBox="0 0 24 24"><path d="M12 20s-8-4.5-8-10.5A4.5 4.5 0 0 1 12 7a4.5 4.5 0 0 1 8 2.5C20 15.5 12 20 12 20z"/></svg></div><h3>Konservierende Zahnheilkunde</h3></div>
    <div class="service"><div class="icon"><svg viewBox="0 0 24 24"><circle cx="12" cy="12" r="3"/><path d="M12 2v3M12 19v3M2 12h3M19 12h3M5 5l2 2M17 17l2 2M5 19l2-2M17 7l2-2"/></svg></div><h3>Zahnärztliche Prothetik</h3></div>
    <div class="service"><div class="icon"><svg viewBox="0 0 24 24"><path d="M3 12h4l3-7 4 14 3-7h4"/></svg></div><h3>Kieferorthopädie</h3></div>
    <div class="service"><div class="icon"><svg viewBox="0 0 24 24"><path d="M3 12h4l3-7 4 14 3-7h4"/></svg></div><h3>Chirurgische Zahnheilkunde</h3></div>
    <div class="service"><div class="icon"><svg viewBox="0 0 24 24"><path d="M2 12s4-7 10-7 10 7 10 7-4 7-10 7S2 12 2 12z"/><circle cx="12" cy="12" r="3"/></svg></div><h3>Ästhetische Zahnheilkunde</h3></div>
    <div class="service"><div class="icon"><svg viewBox="0 0 24 24"><path d="M5 19C5 9 11 5 20 4c0 9-5 15-13 15M5 19l8-8"/></svg></div><h3>Ganzheitliche Zahnheilkunde</h3></div>
    <div class="service"><div class="icon"><svg viewBox="0 0 24 24"><circle cx="12" cy="12" r="9"/><path d="M9 10v.1M15 10v.1M8.5 14.5c2 2 5 2 7 0"/></svg></div><h3>Kinderzahnheilkunde</h3></div>
    <div class="service"><div class="icon"><svg viewBox="0 0 24 24"><circle cx="12" cy="12" r="9"/><path d="M8 12l3 3 5-6"/></svg></div><h3>Bioverträglicher Zahnersatz</h3></div>
  </div>
  <span class="btn green" style="width:134px;margin-top:23px">Alle Leistungen im Detail</span>
</section>

<section class="block labor">
  <div class="team-band"></div>
  <div class="split" style="top:50px">
    <div class="photo" role="img" aria-label="Zahnärztin erklärt einem Kind das Zähneputzen an einem Modell" style="background:linear-gradient(120deg,#f4efe2 0%,#e9e6d8 40%,#d7dfe6 70%,#d9484a 100%)"></div>
    <div class="split-text">
      <h2>Unser Praxislabor</h2>
      <p class="intro">Unsere Praxis verfügt über ein eigenes Praxislabor.</p>
      <p class="body">Durch unser hauseigenes Labor können wir Zahnersatz und Reparaturen schnell und präzise anfertigen. Dies ermöglicht kurze Wartezeiten und eine optimale Anpassung an Ihre individuellen Bedürfnisse.</p>
      <span class="btn">Mehr über unser Labor</span>
    </div>
  </div>
  <div class="split" style="top:345px">
    <div class="split-text">
      <h2>Unser Team</h2>
      <p class="intro">Unser Praxisteam - kompetent, herzlich und darauf fokussiert, Ihre Zahngesundheit bestmöglich zu unterstützen.</p>
      <p class="body">Wir legen großen Wert auf eine vertrauensvolle Atmosphäre und eine individuelle Betreuung. Jedes Teammitglied bringt langjährige Erfahrung und Fachkompetenz mit, um Sie bestmöglich zu versorgen.</p>
      <span class="btn green">Unser Team kennenlernen</span>
    </div>
    <div class="photo" role="img" aria-label="Praxisteam in weißer Kleidung im Grünen" style="background:linear-gradient(180deg,#8aa267 0%,#a9bc8c 35%,#e8edf2 60%,#f3f5f8 100%)"></div>
  </div>
</section>

<section class="block kontakt">
  <h2 class="sec-title center">Kontakt</h2>
  <p class="sec-sub center">So erreichen Sie uns</p>
  <div class="cards">
    <div class="card">
      <h3><svg viewBox="0 0 24 24"><path d="M12 21s-7-6.5-7-12a7 7 0 0 1 14 0c0 5.5-7 12-7 12z"/><circle cx="12" cy="9" r="2.5"/></svg>Adresse</h3>
      Lindenweg 14<br>09217 Talheim-Wiesenau
    </div>
    <div class="card">
      <h3><svg viewBox="0 0 24 24"><path d="M5 3h4l2 5-2.5 1.5a11 11 0 0 0 6 6L16 13l5 2v4a2 2 0 0 1-2 2C10 21 3 14 3 5a2 2 0 0 1 2-2z"/></svg>Telefon &amp; Fax</h3>
      Telefon: 03701-48216<br>Fax: 03701-48217
    </div>
    <div class="card">
      <h3><svg viewBox="0 0 24 24"><rect x="3" y="5" width="18" height="14" rx="2"/><path d="M3 7l9 6 9-6"/></svg>E-Mail</h3>
      <a>info@zahnarztpraxis-kestner.de</a>
    </div>
    <div class="card">
      <h3><svg viewBox="0 0 24 24"><circle cx="12" cy="12" r="9"/><path d="M12 7v5l3 2"/></svg>Online-Eintrag</h3>
      <span class="muted">Informieren Sie sich über Aktualisierungen:</span><br>
      <a style="font-weight:700;font-size:8.5px;display:inline-flex;align-items:center;gap:5px;margin-top:3px">Online-Eintrag <svg class="ext" viewBox="0 0 12 12"><path d="M7 1h4v4M11 1L5 7M9 7v4H1V3h4"/></svg></a>
    </div>
    <div class="card hl-blue">
      <h3>Öffnungszeiten</h3>
      <div class="hours">
        <b>Montag:</b><span>9:00 - 13:00 und 14:00 - 19:00 Uhr</span>
        <b>Dienstag:</b><span>9:00 - 13:00 und 14:00 - 19:00 Uhr</span>
        <b>Mittwoch:</b><span>9:00 - 14:00 Uhr</span>
        <b>Donnerstag:</b><span>geschlossen</span>
        <b>Freitag:</b><span>9:00 - 13:00 Uhr</span>
      </div>
      <p class="note" style="margin-top:9px">... und nach Vereinbarung</p>
    </div>
    <div class="card hl-green">
      <h3>Telefonzeiten</h3>
      <p class="muted" style="margin-bottom:4px">Innerhalb dieser Zeiten sind wir für Sie telefonisch erreichbar:</p>
      <div class="hours">
        <b>Montag:</b><span>9:00 - 15:00 Uhr</span>
        <b>Dienstag:</b><span>9:00 - 15:00 Uhr</span>
        <b>Mittwoch:</b><span>9:00 - 12:00 Uhr</span>
      </div>
      <p class="note" style="margin-top:12px">In dringenden Fällen wenden Sie sich bitte an den zahnärztlichen Notdienst:</p>
      <span class="btn red">Zur Notdienstsuche <svg class="ext" viewBox="0 0 12 12"><path d="M7 1h4v4M11 1L5 7M9 7v4H1V3h4"/></svg></span>
    </div>
  </div>
</section>

<footer class="block footer">
  <div class="foot-left">
    <div class="brand" style="font-size:12px"><i style="width:12px;height:12px"></i>Kestner Dental</div>
    <div class="foot-name">Zahnarztpraxis Dr. Marie Kestner<small>Talheim-Wiesenau</small></div>
  </div>
  <div class="copy">© 2025 Zahnarztpraxis Dr. Marie Kestner<br>Alle Rechte vorbehalten</div>
</footer>

</body>
</html>
```